Coastline Premier Retreats Business Card Design

Design a business card for Coastline Premier Retreats. Look at the website for colors and reference. Card should have logo, name, title, office number, mobile number, email, URL and a tagline like, "Luxury Hotel & Resort Email Marketing" (This might change).

https://www.coastlinepremierretreats.example

The rest I will leave up to your imagination.

Contact Information for Business Card

Logo, name, title, office number, mobile number, email, URL and a tagline like, "Luxury Hotel & Resort Email Marketing" (This might change).

```html
<!DOCTYPE html>
<html lang="en">
<head>
<meta charset="utf-8">
<title>Coastline Premier Retreats – Business Card</title>
<link href="https://fonts.googleapis.com/css2?family=Montserrat:wght@400;500;700;800&display=swap" rel="stylesheet">
<style>
  :root {
    --backdrop: #2a2a2a;
    --card: #1b1b1b;
    --accent: #f07a1a;
    --ink: #ffffff;
    --ink-soft: #e6e6e6;
  }
  * { box-sizing: border-box; margin: 0; padding: 0; }
  html, body {
    width: 1200px; height: 900px; overflow: hidden;
    background: var(--backdrop);
    font-family: "Montserrat", sans-serif;
  }
  .canvas {
    width: 1200px; height: 900px;
    display: flex; flex-direction: column; align-items: center; justify-content: center;
    gap: 36px;
  }
  .card {
    position: relative;
    width: 700px; height: 400px;
    background: var(--card);
    border-bottom: 4px solid var(--accent);
    border-left: 3px solid var(--accent);
    box-shadow: 0 12px 30px rgba(0,0,0,.5);
  }
  /* front */
  .card-front {
    display: flex; flex-direction: column; align-items: center; justify-content: center;
  }
  .brand-name {
    color: var(--ink);
    font-weight: 800;
    text-transform: uppercase;
    letter-spacing: 1px;
    line-height: 1;
  }
  .card-front .brand-name { font-size: 40px; text-align: center; }
  .tagline {
    margin-top: 70px;
    color: var(--accent);
    font-size: 19px;
    font-weight: 500;
    letter-spacing: .5px;
  }
  /* back */
  .card-back .brand-name {
    position: absolute; top: 48px; right: 44px;
    font-size: 21px;
  }
  .person { position: absolute; top: 128px; left: 48px; }
  .person-name {
    color: var(--accent); font-size: 30px; font-weight: 800;
    text-transform: uppercase; letter-spacing: 1px; line-height: 1;
  }
  .person-title { color: var(--ink); font-size: 17px; margin-top: 6px; }
  .person-rule { width: 44px; height: 3px; background: var(--accent); margin-top: 18px; }
  .contacts {
    position: absolute; left: 48px; bottom: 36px;
    list-style: none;
  }
  .contacts li {
    display: flex; align-items: center; gap: 12px;
    color: var(--ink-soft); font-size: 16px; line-height: 27px;
  }
  .contacts svg { width: 14px; height: 14px; fill: var(--accent); flex: none; }
  .address {
    position: absolute; right: 44px; bottom: 40px;
    color: var(--ink-soft); font-size: 16px; line-height: 24px; text-align: right;
  }
</style>
</head>
<body>
<main class="canvas">

  <section class="card card-front" aria-label="Card front">
    <h1 class="brand-name">Coastline Premier Retreats</h1>
    <p class="tagline">Luxury Hotel &amp; Resort Email Marketing</p>
  </section>

  <section class="card card-back" aria-label="Card back">
    <p class="brand-name">Coastline Premier Retreats</p>

    <div class="person">
      <h2 class="person-name">Marcus Hale</h2>
      <p class="person-title">CEO/Founder</p>
      <div class="person-rule"></div>
    </div>

    <ul class="contacts">
      <li>
        <svg viewBox="0 0 14 14" aria-hidden="true"><path d="M4 0h6a1 1 0 0 1 1 1v12a1 1 0 0 1-1 1H4a1 1 0 0 1-1-1V1a1 1 0 0 1 1-1zm0 2v9h6V2zm3 10a.8.8 0 1 0 0 .01z"/></svg>
        555.014.2200
      </li>
      <li>
        <svg viewBox="0 0 14 14" aria-hidden="true"><path d="M1 5c0-2 2.5-3 6-3s6 1 6 3v1H10V4.6C9 4.3 8 4.2 7 4.2s-2 .1-3 .4V6H1zM3 7h8l1.5 5h-11z"/></svg>
        +34 600 000 123
      </li>
      <li>
        <svg viewBox="0 0 14 14" aria-hidden="true"><path d="M0 3h14v9H0zm1.5 1.2L7 8l5.5-3.8V4H1.5z"/></svg>
        info@coastlinepremierretreats.example
      </li>
      <li>
        <svg viewBox="0 0 14 14" aria-hidden="true"><path d="M7 0a7 7 0 1 0 0 14A7 7 0 0 0 7 0zm0 1.5c.8 0 1.7 1.8 1.9 4.5H5.1C5.3 3.3 6.2 1.5 7 1.5zM1.6 8h2.9c.1 1.8.5 3.2 1 4.2A5.5 5.5 0 0 1 1.6 8zm7.9 0h2.9a5.5 5.5 0 0 1-3.9 4.2c.5-1 .9-2.4 1-4.2z"/></svg>
        www.coastlinepremierretreats.example
      </li>
    </ul>

    <address class="address" style="font-style:normal">
      Po Box 48, 210 Harbor Rd<br>
      Bayview, AB 00000
    </address>
  </section>

</main>
</body>
</html>
```